Creation of a page for funnel

Our company is specialized in insoles and well-being. Our insoles help reduce joint problems, stress or ink to promote weight loss. We need a clean and refined sales page, this one will be used on funnel click. The page should display the values of our product in first: "promote weight loss" in second: "Relieves muscle and joint pain" third: "Increases energy and stress stress". The page must be in the colors of our logo (green) if possible this color: light green: dark green 54c248. It is important to follow this model for the page with totally new and fresh desing: https: // lunar-pebble. uk / qtw-lr Additionnal details for icons Section u: 1: "A unique design based on two types of knowledge" 2: "approved by acupressure expert" "Lose weight" 2: "Increases blood flow and oxygen in your body" 3: "Relieves muscle and joint pain" 4: "Increases energy and reduces stress" Section x: 1: "for men and women" 2: "one size "3:" Adjustable by cutting "Section y: 1:" powerful magnet in tourmaline "2:" for all type of shoes "3:" Flexible and light "4:" Breathable "Section z: 1:" free shipping "2 : "Customer service" 3: "money back guarantee" 4: "safe payment"
Target Market(s)
men and women 35
Number of Pages Required
1 page
Requirements
Must have
- the 5 sections mentioned in description
Nice to have
- some GIF like the funnel

```html
<!DOCTYPE html>
<html lang="en">
<head>
<meta charset="utf-8">
<title>StrideLeaf – Insoles for well-being</title>
<link href="https://fonts.googleapis.com/css2?family=Roboto:wght@400;500;700&family=Open+Sans:wght@400;600&family=Oswald:wght@500&family=Montserrat:wght@400;500&display=swap" rel="stylesheet">
<style>
:root{
  --green:#3a9b0a;
  --green-light:#54c248;
  --dark:#3d3d3d;
  --ink:#222;
  --text:#444;
  --grey-bg:#f2f2f2;
  --white:#fff;
  --black:#000;
}
*{margin:0;padding:0;box-sizing:border-box}
html,body{width:1200px;height:5080px;overflow:hidden;background:var(--white)}
body{font-family:"Open Sans",sans-serif;color:var(--text)}
.page{position:relative;width:1200px;height:5080px;overflow:hidden}
.abs{position:absolute}

/* header */
.brand{left:90px;top:28px;display:flex;align-items:center;gap:12px}
.brand-dot{width:40px;height:40px;border-radius:50%;background:var(--green)}
.brand-name{font-family:"Roboto",sans-serif;font-size:46px;font-weight:500;color:var(--dark);line-height:1}
.brand-tag{left:155px;top:84px;font-family:"Roboto",sans-serif;font-size:20px;color:var(--ink)}
.topbar{left:660px;top:0;height:36px;display:flex}
.topbar .phone{background:var(--dark);color:#fff;width:180px;font:500 16px "Roboto",sans-serif;display:flex;align-items:center;justify-content:center;clip-path:polygon(8% 0,100% 0,100% 100%,0 100%)}
.topbar .shop{background:var(--green);color:#fff;width:190px;font:500 16px "Roboto",sans-serif;display:flex;align-items:center;justify-content:center;clip-path:polygon(0 0,100% 0,92% 100%,0 100%)}
.nav{top:76px;left:632px;display:flex;gap:28px;font:500 16px "Roboto",sans-serif;color:var(--ink)}

/* hero */
.hero-photo{left:0;top:137px;width:1200px;height:650px}
.hero-title{left:86px;top:262px;font:700 76px "Roboto",sans-serif;color:#fff;text-shadow:3px 3px 0 var(--green)}
.hero-sub{left:86px;top:358px;font:400 40px "Roboto",sans-serif;color:#fff}
.btn{display:flex;align-items:center;justify-content:center;border-radius:30px;color:#fff;font:500 25px "Roboto",sans-serif}
.hero-btn{left:90px;top:438px;width:178px;height:60px;background:var(--green)}

/* welcome */
.welcome-title{left:0;top:880px;width:1200px;text-align:center;font:400 42px "Roboto",sans-serif;color:var(--ink)}
.welcome-title b{font-weight:700}
.welcome-title .accent{color:var(--green);font-weight:700}
.welcome-text{left:150px;top:950px;width:900px;text-align:center;font-size:15px;line-height:30px;color:#333}
.card{top:1114px;width:258px;height:268px;padding:60px 22px 0;text-align:center;font-family:Arial,sans-serif;font-size:13px;line-height:26px;box-shadow:0 4px 10px rgba(0,0,0,.2)}
.card svg{display:block;margin:0 auto 10px}
.card h3{font-size:13px;font-weight:400;line-height:22px;margin-bottom:14px}
.card-dark{left:172px;background:var(--dark);color:#fff}
.card-light{left:470px;background:#f4f4f4;color:#555}
.card-green{left:770px;background:var(--green);color:#fff}

/* funnel */
.row{left:90px;width:1020px;background:linear-gradient(#fafafa,#e8e8e8)}
.row-num{position:absolute;left:78px;font:500 48px "Roboto",sans-serif;color:#333}
.funnel-label{width:300px;text-align:center;color:#fff;font:500 27px/38px "Roboto",sans-serif}
.funnel-btn{left:510px;top:1980px;width:180px;height:54px;background:var(--dark)}

/* benefits panel */
.benefit-photo{left:563px;top:2145px;width:637px;height:640px}
.benefit-green{left:0;top:2145px;width:563px;height:640px;background:var(--green)}
.benefit-title{left:90px;top:2255px;font:700 41px/48px "Roboto",sans-serif;color:#fff}
.benefit-text{left:90px;top:2358px;width:340px;font-size:14px;line-height:28px;color:#fff}
.benefit-bar{left:90px;top:2533px;width:155px;height:6px;background:#fff;border-radius:3px}
.panel{left:456px;top:2212px;width:654px;height:508px;background:#fff}
.feat{position:absolute;width:200px}
.feat h4{font:500 13px/21px "Oswald",sans-serif;color:#222;margin:8px 0 12px;text-transform:uppercase}
.feat p{font-size:10px;line-height:16px;color:#666}

/* product */
.product{left:0;top:2785px;width:1200px;height:530px;background:var(--grey-bg)}
.product-title{left:0;top:2878px;width:1200px;text-align:center;font:500 40px "Roboto",sans-serif;color:var(--ink)}
.tile{top:2972px;width:322px}
.tile .img{height:183px}
.tile .label{height:50px;background:var(--green);color:#fff;display:flex;align-items:center;justify-content:center;font:700 20px "Roboto",sans-serif}

/* features list */
.feet-art{left:90px;top:3410px;width:430px;height:620px;border-radius:50%/40%;background:radial-gradient(circle at 50% 45%,#8fdc2a,#3a9b0a 70%,#fff 71%)}
.perk{left:638px;display:flex;align-items:center;gap:18px;font:500 24px "Roboto",sans-serif;color:#333}
.perk-icon{width:92px;height:92px;border-radius:50%;background:var(--green);display:flex;align-items:center;justify-content:center}

/* guarantees */
.service{top:4250px;width:240px;text-align:center;font:500 24px "Roboto",sans-serif;color:#333}
.service .ring{width:162px;height:162px;border:2px solid #999;border-radius:50%;margin:0 auto 30px;display:flex;align-items:center;justify-content:center}

/* footer */
.footer-bg{left:0;top:4600px;width:1200px;height:480px}
.fcol{top:4740px;color:#fff;font-family:"Montserrat",sans-serif}
.fcol h5{font:500 20px "Montserrat",sans-serif;margin-bottom:14px;text-transform:none}
.fcol a,.fcol p{display:block;font-size:15px;line-height:33px;color:#fff;text-decoration:none}
.contact-item{display:flex;gap:18px;margin-bottom:20px;font-size:15px;line-height:21px}
.c-icon{width:28px;height:28px;border:2px solid #fff;border-radius:50%;flex:none;display:flex;align-items:center;justify-content:center}
.social{display:flex;align-items:center;gap:12px;font-size:15px;line-height:42px}
.social span.dot{width:28px;height:28px;border:2px solid #fff;border-radius:50%}
.subscribe{display:flex;margin-top:18px;width:236px;height:34px}
.subscribe input{flex:1;border:none;padding:0 10px;font:11px "Montserrat",sans-serif;color:#777}
.subscribe button{width:50px;border:none;background:var(--green);color:#fff}
.copyright{left:0;top:5020px;width:1200px;text-align:center;font:500 15px "Montserrat",sans-serif;color:#fff}
</style>
</head>
<body>
<div class="page">

  <!-- header -->
  <div class="abs brand"><span class="brand-dot"></span><span class="brand-name">StrideLeaf</span></div>
  <div class="abs brand-tag">L’essayer c’est l’adopter !</div>
  <div class="abs topbar"><span class="phone">555 010 2040</span><span class="shop">Shop Now</span></div>
  <nav class="abs nav"><span>How It Works</span><span>Products</span><span>Pricing</span><span>Faq</span><span>Contact Us</span></nav>

  <!-- hero -->
  <svg class="abs hero-photo" viewBox="0 0 1200 650" role="img" aria-label="Photo of a hand fitting a green insole under a bare foot">
    <defs>
      <linearGradient id="heroGrad" x1="0" y1="0" x2="1" y2="1">
        <stop offset="0" stop-color="#8a8a88"/><stop offset=".5" stop-color="#d7cfc8"/><stop offset="1" stop-color="#c8a690"/>
      </linearGradient>
    </defs>
    <path d="M0 0H1200V560Q600 660 0 550Z" fill="url(#heroGrad)"/>
    <path d="M0 555Q600 690 1200 545V560Q600 660 0 565Z" fill="#3a9b0a"/>
  </svg>
  <div class="abs hero-title">Stride Leaf</div>
  <div class="abs hero-sub">Relieve pain, Lose weight</div>
  <div class="abs btn hero-btn">Shop Now</div>

  <!-- welcome -->
  <h1 class="abs welcome-title">Welcome to <b>Stride</b> <span class="accent">Leaf</span></h1>
  <p class="abs welcome-text">Lorem Ipsum is simply dummy text of the printing and typesetting industry. Lorem Ipsum has been the industry's standard dummy text ever since the 1500s, when an unknown printer took a galley of type and scrambled it to make a type specimen book. It has survived not only five centuries, but also the leap into electronic typesetting, remaining essentially unchanged.</p>

  <div class="abs card card-dark">
    <svg width="60" height="56" viewBox="0 0 60 56" fill="none" stroke="#fff" stroke-width="2"><path d="M30 44l-14-14a8 8 0 0 1 14-8 8 8 0 0 1 14 8z"/><path d="M6 20h10M44 36h10"/></svg>
    <h3>A totally natural solution without any health risk</h3>
    <p>Lorem Ipsum is simply dummy text of the printing and typesetting industry.</p>
  </div>
  <div class="abs card card-light">
    <svg width="60" height="56" viewBox="0 0 60 56" fill="none" stroke="#333" stroke-width="2"><rect x="20" y="6" width="20" height="44" rx="3"/><path d="M24 16h12M24 24h12"/></svg>
    <h3>approved by acupressure expert</h3>
    <p>Lorem Ipsum is simply dummy text of the printing and typesetting industry.</p>
  </div>
  <div class="abs card card-green">
    <svg width="60" height="56" viewBox="0 0 60 56" fill="none" stroke="#fff" stroke-width="2"><circle cx="30" cy="22" r="10"/><path d="M26 34h8M26 40h8M10 48h40M30 4v4M12 22h4M44 22h4"/></svg>
    <h3>A unique design based on two types of knowledge</h3>
    <p>Lorem Ipsum is simply dummy text of the printing and typesetting industry.</p>
  </div>

  <!-- funnel -->
  <div class="abs row" style="top:1490px;height:135px"><span class="row-num" style="top:36px">01</span></div>
  <div class="abs row" style="top:1625px;height:137px"><span class="row-num" style="top:38px">02</span></div>
  <div class="abs row" style="top:1762px;height:146px"><span class="row-num" style="top:42px">03</span></div>
  <svg class="abs" style="left:335px;top:1490px" width="532" height="418" viewBox="0 0 532 418">
    <polygon points="0,0 531,0 474,135 57,135" fill="#3a9b0a"/>
    <polygon points="57,135 474,135 416,272 115,272" fill="#3d3d3d"/>
    <polygon points="115,272 416,272 355,418 177,418" fill="#3a9b0a"/>
  </svg>
  <div class="abs funnel-label" style="left:451px;top:1514px">Increases energy and reduces stress</div>
  <div class="abs funnel-label" style="left:451px;top:1648px">Relieves muscle and joint pain</div>
  <div class="abs funnel-label" style="left:451px;top:1792px">promote weight loss</div>
  <svg class="abs" style="left:965px;top:1528px" width="62" height="62" viewBox="0 0 62 62" fill="none" stroke="#222" stroke-width="2"><path d="M18 56V42C8 36 8 18 22 10c14-8 32 2 30 18l6 10h-6v10H40v8"/><path d="M28 22l6 8-6 4 8 8"/></svg>
  <svg class="abs" style="left:965px;top:1665px" width="62" height="62" viewBox="0 0 62 62" fill="none" stroke="#222" stroke-width="2"><rect x="4" y="24" width="24" height="30" rx="6"/><rect x="36" y="6" width="16" height="20" rx="4"/><path d="M36 44h16M38 40v8M50 40v8"/></svg>
  <svg class="abs" style="left:965px;top:1808px" width="62" height="62" viewBox="0 0 62 62" fill="none" stroke="#222" stroke-width="2"><path d="M16 4c4 10 4 16 0 24 4 12 2 20 0 30h30c-2-10-4-18 0-30-4-8-4-14 0-24"/><path d="M4 14h8M8 10l-4 4 4 4M50 14h8M54 10l4 4-4 4"/></svg>
  <div class="abs btn funnel-btn">Shop Now</div>

  <!-- benefits -->
  <div class="abs benefit-photo" role="img" aria-label="Photo of people exercising together" style="background:linear-gradient(135deg,#3a3330,#6b5346 50%,#2a2624)"></div>
  <div class="abs benefit-green"></div>
  <h2 class="abs benefit-title">With our product,<br>you can</h2>
  <p class="abs benefit-text">Lorem Ipsum is simply dummy text of the printing and typesetting industry. Lorem Ipsum has been the industry's standard dummy text ever since the 1500s</p>
  <div class="abs benefit-bar"></div>
  <div class="abs panel">
    <div class="feat" style="left:104px;top:88px">
      <svg width="58" height="58" viewBox="0 0 62 62" fill="none" stroke="#222" stroke-width="2"><path d="M16 4c4 10 4 16 0 24 4 12 2 20 0 30h30c-2-10-4-18 0-30-4-8-4-14 0-24"/><path d="M4 14h8M50 14h8"/></svg>
      <h4>Lose weight</h4>
      <p>Lorem Ipsum has been the industry's standard dummy text ever since the 1500s.</p>
    </div>
    <div class="feat" style="left:362px;top:88px">
      <svg width="58" height="58" viewBox="0 0 62 62" fill="none" stroke="#222" stroke-width="2"><circle cx="31" cy="26" r="20"/><path d="M22 26h18M31 17v18M20 48v10h22V48"/></svg>
      <h4>Increases blood flow and oxygen throughout your body</h4>
      <p>Lorem Ipsum has been the industry's standard dummy text ever since the 1500s.</p>
    </div>
    <div class="feat" style="left:104px;top:272px">
      <svg width="70" height="50" viewBox="0 0 70 50" fill="none" stroke="#222" stroke-width="2"><path d="M4 30c20-20 40-24 60-14-8 10-30 16-60 14z"/><circle cx="50" cy="22" r="10"/></svg>
      <h4>Relieves muscle and joint pain</h4>
      <p>Lorem Ipsum has been the industry's standard dummy text ever since the 1500s.</p>
    </div>
    <div class="feat" style="left:362px;top:264px">
      <svg width="58" height="62" viewBox="0 0 62 62" fill="none" stroke="#222" stroke-width="2"><path d="M18 58V44C8 38 8 20 22 12c14-8 32 2 30 18l6 10h-6v10H40v8"/><path d="M30 22l6 8-6 4 8 8"/></svg>
      <h4>Increases energy and reduces stress</h4>
      <p>Lorem Ipsum has been the industry's standard dummy text ever since the 1500s.</p>
    </div>
  </div>

  <!-- product facts -->
  <div class="abs product"></div>
  <h2 class="abs product-title">Increases energy and reduces stress</h2>
  <div class="abs tile" style="left:91px"><div class="img" role="img" aria-label="Photo of men's and women's shoes with insoles" style="background:linear-gradient(90deg,#2b2b2b,#e07a2a 25%,#7b5540 55%,#e06b1a 85%,#fff)"></div><div class="label">FOR MEN AND WOMEN</div></div>
  <div class="abs tile" style="left:441px"><div class="img" role="img" aria-label="Photo of a pair of perforated insoles" style="background:linear-gradient(90deg,#3b3f47,#ddd6ca 30%,#e8e2d8 70%,#3b3f47)"></div><div class="label">ONE SIZE</div></div>
  <div class="abs tile" style="left:790px"><div class="img" role="img" aria-label="Photo of an insole being trimmed with scissors" style="background:linear-gradient(135deg,#5a7fa8,#c44b3a 45%,#d8b08a)"></div><div class="label">ADJUSTABLE BY CUTTING</div></div>

  <!-- perks -->
  <div class="abs feet-art" role="img" aria-label="Illustration of two green footprints"></div>
  <div class="abs perk" style="top:3484px"><span class="perk-icon"><svg width="50" height="40" viewBox="0 0 50 40" fill="none" stroke="#fff" stroke-width="2"><path d="M14 4v20c0 6 4 10 10 10h22c0-6-8-8-14-10L24 4"/></svg></span>powerful magnet in tourmaline</div>
  <div class="abs perk" style="top:3609px"><span class="perk-icon"><svg width="50" height="40" viewBox="0 0 50 40" fill="none" stroke="#fff" stroke-width="2"><path d="M6 10c6 0 10 18 28 22h10v4H14v-6M6 10v26"/></svg></span>for all type of shoes</div>
  <div class="abs perk" style="top:3726px"><span class="perk-icon"><svg width="44" height="44" viewBox="0 0 44 44" fill="none" stroke="#fff" stroke-width="2"><circle cx="22" cy="20" r="9"/><path d="M18 32h8M19 37h6M22 3v5M6 20h5M33 20h5M10 8l4 4M34 8l-4 4"/></svg></span>Flexible and light</div>
  <div class="abs perk" style="top:3851px"><span class="perk-icon"><svg width="44" height="44" viewBox="0 0 44 44" fill="none" stroke="#fff" stroke-width="2"><path d="M6 10h32M6 18h32"/><circle cx="12" cy="32" r="5"/><circle cx="22" cy="32" r="5"/><circle cx="32" cy="32" r="5"/></svg></span>Breathable</div>

  <!-- guarantees -->
  <div class="abs service" style="left:53px"><div class="ring"><svg width="110" height="70" viewBox="0 0 110 70" fill="none" stroke="#3a9b0a" stroke-width="3"><rect x="36" y="6" width="68" height="40"/><path d="M36 20H14L4 34v16h32M104 46v4H36"/><circle cx="20" cy="54" r="7"/><circle cx="84" cy="54" r="7"/></svg></div>Free Shipping</div>
  <div class="abs service" style="left:320px"><div class="ring"><svg width="80" height="80" viewBox="0 0 80 80" fill="none" stroke="#3a9b0a" stroke-width="3"><circle cx="40" cy="30" r="16"/><path d="M14 76c0-14 12-24 26-24s26 10 26 24M22 30v-4a18 18 0 0 1 36 0v4"/></svg></div>Customer Service</div>
  <div class="abs service" style="left:613px"><div class="ring"><svg width="90" height="80" viewBox="0 0 90 80" fill="none" stroke="#3a9b0a" stroke-width="3"><rect x="30" y="6" width="40" height="8"/><circle cx="50" cy="36" r="14"/><path d="M50 28v16M4 56h20l16 10h30l16-12M4 76h20"/></svg></div>Money Back Guarantee</div>
  <div class="abs service" style="left:908px"><div class="ring"><svg width="70" height="90" viewBox="0 0 70 90" fill="none" stroke="#3a9b0a" stroke-width="3"><path d="M6 26a29 22 0 0 1 58 0zM35 26v16"/><path d="M24 52c-8 10-8 32 11 32s19-22 11-32z"/><path d="M35 58v20"/></svg></div>Safe Payment</div>

  <!-- footer -->
  <svg class="abs footer-bg" viewBox="0 0 1200 480" preserveAspectRatio="none">
    <path d="M0 78Q600 -30 1200 78V480H0Z" fill="#000"/>
    <path d="M0 78Q600 -40 1200 78Q600 -22 0 78Z" fill="#3a9b0a"/>
  </svg>
  <div class="abs fcol" style="left:90px;top:4744px">
    <h5>CONTACT US</h5>
    <div class="contact-item"><span class="c-icon"><svg width="12" height="16" viewBox="0 0 12 16"><path d="M6 1a5 5 0 0 0-5 5c0 4 5 9 5 9s5-5 5-9a5 5 0 0 0-5-5z" fill="none" stroke="#fff" stroke-width="1.5"/><circle cx="6" cy="6" r="1.6" fill="#fff"/></svg></span><span>Address :<br>14 Meadow Lane,<br>Fernbrook, OR 97001</span></div>
    <div class="contact-item"><span class="c-icon"><svg width="14" height="14" viewBox="0 0 14 14"><path d="M3 1l2 3-1.5 1.5a8 8 0 0 0 5 5L10 9l3 2-1.5 2.5C6 13 1 8 .5 2.5z" fill="#fff"/></svg></span><span>Call Us :<br>555 010 2040</span></div>
    <div class="contact-item"><span class="c-icon"><svg width="14" height="10" viewBox="0 0 14 10" fill="none" stroke="#fff" stroke-width="1.5"><rect x="1" y="1" width="12" height="8"/><path d="M1 1l6 5 6-5"/></svg></span><span>E - Mail Us :<br>hello@strideleaf.example</span></div>
  </div>
  <div class="abs fcol" style="left:386px;top:4736px">
    <h5>Quick Links</h5>
    <a>How It Works</a><a>Products</a><a>Pricing</a><a>Faq</a><a>Contact Us</a>
  </div>
  <div class="abs fcol" style="left:624px;top:4736px">
    <h5>GET IN TOUCH</h5>
    <div class="social"><span class="dot"></span>Townsquare</div>
    <div class="social"><span class="dot"></span>Birdnote</div>
    <div class="social"><span class="dot"></span>Workring</div>
    <div class="social"><span class="dot"></span>Photoreel</div>
  </div>
  <div class="abs fcol" style="left:877px;top:4736px;width:240px">
    <h5>Newsletter</h5>
    <p style="line-height:22px">Lorem Ipsum has been the industry's standard dummy text ever since the 1500s.</p>
    <div class="subscribe"><input type="text" placeholder="Enter your email address"><button aria-label="Subscribe"><svg width="14" height="10" viewBox="0 0 14 10" fill="none" stroke="#fff" stroke-width="1.5"><path d="M1 5h11M8 1l4 4-4 4"/></svg></button></div>
  </div>
  <div class="abs copyright">© 2019 Copyrights | All Rights Reserved</div>

</div>
</body>
</html>
```